Harborline Renewal Business Card Design

Professional and clean design. The design colors should flow with the logo. Two-sided card with the website on the back which is:

www.HarborlineRenewal.example.

"Specializing in Water Damage Restoration"

On the front I need the name, email, phone, and logo.

Name: Darnell Quisby
Email: Darnell@HarborlineRenewal.example
Phone: 555-318-2046 for now

I only have the Preview and Thumbnail right now but should have the source files uploaded within a day or two.

Target Market(s)

Flood victims, home owners with water damage from busted pipes etc...

Industry/Entity Type

Business

Contact Information for Business Card

Name: Darnell Quisby

Font styles to use
Serif
Sans Serif

Requirements
Must have
• Business Card Details Info

```html
<!DOCTYPE html>
<html lang="en">
<head>
<meta charset="utf-8">
<title>Harborline Renewal Business Card</title>
<link rel="stylesheet" href="https://fonts.googleapis.com/css2?family=Marcellus+SC&family=Open+Sans:wght@400&display=swap">
<style>
  :root {
    --brand-blue: #2b96d4;
    --wordmark-blue: #2a8fcd;
    --wave-blue: #58bfec;
    --card-white: #ffffff;
    --ink: #2f2f2f;
    --backdrop: #eef1f4;
    --card-edge: #4a4a4a;
  }
  * { margin: 0; padding: 0; box-sizing: border-box; }
  html, body {
    width: 1200px; height: 1075px; overflow: hidden;
    background: var(--backdrop);
  }
  .canvas { position: relative; width: 1200px; height: 1075px; }

  .card {
    position: absolute;
    border-radius: 36px;
    overflow: hidden;
  }
  .card-front {
    left: 325px; top: 40px; width: 842px; height: 483px;
    background: var(--card-white);
    border: 1px solid var(--card-edge);
  }
  .card-back {
    left: 34px; top: 555px; width: 843px; height: 480px;
    background: var(--brand-blue);
  }

  .front-waves { position: absolute; inset: 0; width: 100%; height: 100%; }

  .brand-mark {
    position: absolute; left: 200px; top: 20px; width: 110px; height: 110px;
    border-radius: 50%; background: var(--brand-blue);
  }
  .brand-name {
    position: absolute; left: 0; width: 510px; top: 150px;
    text-align: center;
    font-family: "Marcellus SC", serif;
    font-size: 46px; letter-spacing: 2px;
    color: var(--wordmark-blue);
    line-height: 1.1;
  }
  .person {
    position: absolute; left: 0; width: 510px; top: 280px;
    text-align: center;
    font-family: "Marcellus SC", serif;
    color: var(--wordmark-blue);
  }
  .person-name { font-size: 31px; letter-spacing: 1px; line-height: 1.1; }
  .person-title { font-size: 25px; color: var(--ink); letter-spacing: 2px; margin-top: 2px; }

  .contact-list {
    position: absolute; right: 14px; top: 360px;
    list-style: none;
    font-family: "Open Sans", sans-serif;
    font-size: 20px; color: var(--card-white);
    text-align: right;
  }
  .contact-list li {
    display: flex; justify-content: flex-end; align-items: center;
    gap: 8px; height: 32px;
  }
  .contact-icon { width: 18px; height: 18px; flex: none; }

  .back-mark {
    position: absolute; left: 331px; top: 60px; width: 180px; height: 180px;
    border-radius: 50%; background: var(--card-white);
  }
  .back-brand-name {
    position: absolute; left: 0; width: 100%; top: 262px;
    text-align: center;
    font-family: "Marcellus SC", serif;
    font-size: 44px; letter-spacing: 2px; color: var(--card-white);
  }
  .tagline {
    position: absolute; left: 0; width: 630px; top: 374px;
    text-align: center;
    font-family: "Marcellus SC", serif;
    font-size: 25px; letter-spacing: 1px; color: var(--card-white);
  }
</style>
</head>
<body>
<main class="canvas">

  <section class="card card-front" aria-label="Card front">
    <svg class="front-waves" viewBox="0 0 732 420" preserveAspectRatio="none" aria-hidden="true">
      <path d="M0,307 C180,365 400,340 520,228 C400,325 200,368 0,345 Z" fill="var(--wave-blue)"/>
      <path d="M0,360 C260,400 520,320 732,18 L732,420 L0,420 Z" fill="var(--brand-blue)"/>
    </svg>

    <div class="brand-mark" aria-hidden="true"></div>
    <h1 class="brand-name">Harborline Renewal</h1>

    <div class="person">
      <p class="person-name">Darnell Quisby</p>
      <p class="person-title">Title</p>
    </div>

    <ul class="contact-list">
      <li>
        <svg class="contact-icon" viewBox="0 0 20 20" aria-hidden="true">
          <circle cx="10" cy="10" r="9" fill="none" stroke="#fff" stroke-width="1.6"/>
          <path d="M7 5 L9 5 L9.8 8 L8.6 9 C9.3 10.6 10.2 11.5 11.3 12.1 L12.3 11 L15 11.8 L15 13.8 C10 14.5 6.2 10.5 7 5 Z" fill="#fff"/>
        </svg>
        <span>555-318-2046</span>
      </li>
      <li>
        <svg class="contact-icon" viewBox="0 0 20 20" aria-hidden="true">
          <rect x="2" y="5" width="16" height="11" rx="1.5" fill="#fff"/>
          <path d="M2.5 6 L10 11 L17.5 6" fill="none" stroke="var(--brand-blue)" stroke-width="1.6"/>
        </svg>
        <span>Darnell@HarborlineRenewal.example</span>
      </li>
      <li>
        <svg class="contact-icon" viewBox="0 0 20 20" aria-hidden="true">
          <g fill="none" stroke="#fff" stroke-width="1.4">
            <circle cx="10" cy="10" r="8"/>
            <ellipse cx="10" cy="10" rx="3.5" ry="8"/>
            <path d="M2 10 H18 M3.5 6 H16.5 M3.5 14 H16.5"/>
          </g>
        </svg>
        <span>www.HarborlineRenewal.example</span>
      </li>
    </ul>
  </section>

  <section class="card card-back" aria-label="Card back">
    <div class="back-mark" aria-hidden="true"></div>
    <p class="back-brand-name">Harborline Renewal</p>
    <p class="tagline">Specializing in Water Damage Restoration</p>
  </section>

</main>
</body>
</html>
```